Design some Business Cards for Tavro

Thanks to everyone for their efforts. I will just be reviewing the first two entries from each contestant, so I'd suggest withdrawing entries which are not your favorites & going with your best two. Many thanks, Dorian

I was after a double sided business card for tavro.com.au. Tavro is a billing app and website for tradesman and service providers who move from site to site.

Firstly design for Dorian Webb with mobile 0487 555 904 & email demo@tavro.com.au.

Logo is attached, so please work with those colours. I've also included our url if you believe that is worth building in.

I would like the original working files and the business card will need to be produced for 3 different employees when the winner is selected.

Additional TAVRO text files if this helps.

```html
<!DOCTYPE html>
<html lang="en">
<head>
<meta charset="utf-8">
<title>Tavro Business Cards</title>
<link href="https://fonts.googleapis.com/css2?family=Open+Sans:wght@400;600;700&display=swap" rel="stylesheet">
<style>
  :root {
    --backdrop: #3a3a3a;
    --brand-blue: #23a7d6;
    --brand-blue-dark: #1793c4;
    --brand-red: #d9262c;
    --ink: #1f1f2a;
    --paper: #ffffff;
    --rule: #d8d8d8;
  }
  html, body {
    margin: 0;
    padding: 0;
    width: 1200px;
    height: 851px;
    overflow: hidden;
    background: var(--backdrop);
    font-family: "Open Sans", sans-serif;
  }
  .canvas {
    position: relative;
    width: 1200px;
    height: 851px;
  }
  .card {
    position: absolute;
    top: 265px;
    width: 540px;
    height: 320px;
    border-radius: 26px;
    overflow: hidden;
  }
  .card--front { left: 40px; background: var(--brand-blue); }
  .card--back { left: 620px; background: var(--paper); }

  .brand {
    position: absolute;
    display: flex;
    align-items: center;
    gap: 12px;
  }
  .brand__dot {
    width: 46px;
    height: 46px;
    border-radius: 50%;
    background: var(--paper);
  }
  .brand__name {
    font-weight: 600;
    font-size: 54px;
    letter-spacing: 2px;
    line-height: 1;
  }
  .card--front .brand { left: 238px; top: 176px; }
  .card--front .brand__name { color: var(--ink); }
  .card--front .brand__dot { background: var(--paper); }

  .front__url {
    position: absolute;
    left: 300px;
    top: 244px;
    color: var(--brand-red);
    font-size: 15px;
    letter-spacing: 1px;
  }

  .card--back .brand { left: 34px; top: 92px; }
  .card--back .brand__name { color: var(--brand-blue); }
  .card--back .brand__dot {
    background: var(--paper);
    border: 3px solid var(--brand-red);
    width: 42px;
    height: 42px;
  }
  .back__divider {
    position: absolute;
    left: 298px;
    top: 70px;
    width: 1px;
    height: 120px;
    background: var(--rule);
  }
  .contact {
    position: absolute;
    left: 316px;
    top: 78px;
  }
  .contact__name {
    margin: 0;
    color: var(--brand-blue);
    font-weight: 700;
    font-size: 21px;
    line-height: 1.1;
  }
  .contact__role {
    margin: 0 0 10px;
    color: var(--brand-red);
    font-size: 17px;
  }
  .contact__list {
    list-style: none;
    margin: 0;
    padding: 0;
  }
  .contact__item {
    display: flex;
    align-items: center;
    gap: 8px;
    font-size: 14px;
    color: var(--ink);
    line-height: 21px;
  }
  .contact__icon {
    width: 13px;
    height: 13px;
    flex: none;
  }
  .back__wave {
    position: absolute;
    left: 0;
    bottom: 0;
    width: 540px;
    height: 320px;
  }
</style>
</head>
<body>
<main class="canvas">

  <section class="card card--front" aria-label="Card front">
    <div class="brand">
      <span class="brand__dot"></span>
      <span class="brand__name">TAVRO</span>
    </div>
    <div class="front__url">WWW.TAVRO.COM.AU</div>
  </section>

  <section class="card card--back" aria-label="Card back">
    <svg class="back__wave" viewBox="0 0 540 320" aria-hidden="true">
      <path d="M0 222 C 120 200, 230 220, 330 262 S 480 312, 540 306 L540 320 L0 320 Z" fill="var(--brand-blue)"/>
      <path d="M0 222 C 120 200, 230 220, 330 262 S 480 312, 540 306" fill="none" stroke="var(--brand-red)" stroke-width="4"/>
    </svg>

    <div class="brand">
      <span class="brand__dot"></span>
      <span class="brand__name">TAVRO</span>
    </div>

    <div class="back__divider"></div>

    <div class="contact">
      <p class="contact__name">Dorian Webb</p>
      <p class="contact__role">Director</p>
      <ul class="contact__list">
        <li class="contact__item">
          <svg class="contact__icon" viewBox="0 0 16 16" aria-hidden="true"><circle cx="8" cy="8" r="8" fill="var(--brand-blue-dark)"/><path d="M5 4.5l1.6-.5 1 2.2-1 .8c.5 1 1.2 1.7 2.2 2.2l.8-1 2.2 1-.5 1.6c-3.3.2-6.5-3-6.3-6.3z" fill="#fff"/></svg>
          0487 555 904
        </li>
        <li class="contact__item">
          <svg class="contact__icon" viewBox="0 0 16 16" aria-hidden="true"><rect x="1" y="3" width="14" height="10" rx="1.5" fill="var(--brand-blue-dark)"/><path d="M2 4.5l6 4.5 6-4.5" fill="none" stroke="#fff" stroke-width="1.2"/></svg>
          dorian@tavro.com.au
        </li>
        <li class="contact__item">
          <svg class="contact__icon" viewBox="0 0 16 16" aria-hidden="true"><circle cx="8" cy="8" r="7" fill="var(--brand-blue-dark)"/><path d="M1 8h14M8 1c-3 3.5-3 10.5 0 14M8 1c3 3.5 3 10.5 0 14" fill="none" stroke="#fff" stroke-width="1"/></svg>
          www.tavro.com.au
        </li>
      </ul>
    </div>
  </section>

</main>
</body>
</html>
```